Detail Shop Business card design

i need a business card design for my new detailing company called 'Brisk's Polish Works'. i want an all black and white design . simple, direct and to the point. i want the designer to choose a fitting font to match the logothe front should have logo, address, phone and email and the back side should have a slogan and text indicating that we offer services on anything including cars, trucks, motorcycles and RVs. slogan will read "We make every mile shine"
maybe also very small on the back side the IG icon with Brisks_Polish_Works

phone 208.417.6352
address 3847 E Larkin Ave
Carrow Falls ID 83714
email: BrisksPolish@mailvexo.com

Target Market(s)

all ages , auto enthusiasts

Industry/Entity Type

Automotive

Contact Information for Business Card

the front should have logo, address, phone and email and the back side should have a slogan and text indicating that we offer services on anything including cars, trucks, motorcycles and RVs. slogan will read "We make every mile shine"

phone 208.417.6352
address 3847 E Larkin Ave
Carrow Falls ID 83714

Colors
000000
ffffff

Requirements
Must have
• bold font and very simple design with good spacing
Nice to have
• anything creative from the designer indicating we service any types of vehicles
Should not have
• any colors ,

```html
<!DOCTYPE html>
<html lang="en">
<head>
<meta charset="utf-8">
<title>Brisk's Polish Works – Business Card</title>
<link rel="stylesheet" href="https://fonts.googleapis.com/css2?family=PT+Sans:wght@400;700&family=PT+Sans+Narrow:wght@400;700&display=swap">
<style>
  :root {
    --backdrop: #d9d7d4;
    --card: #121212;
    --ink: #ffffff;
    --ink-soft: #d6d6d6;
    --ink-muted: #a9a9a9;
  }
  * { margin: 0; padding: 0; box-sizing: border-box; }
  html, body {
    width: 1200px; height: 864px; overflow: hidden;
    background: var(--backdrop);
  }
  .canvas {
    position: relative; width: 1200px; height: 864px;
    display: flex; align-items: center; justify-content: center; gap: 40px;
  }
  .card {
    width: 540px; height: 309px;
    background: var(--card);
    color: var(--ink);
    position: relative;
    box-shadow: 0 12px 30px rgba(0,0,0,.25);
  }

  /* Logo side */
  .card--brand {
    display: flex; flex-direction: column; align-items: center; justify-content: center;
    font-family: "PT Sans Narrow", sans-serif;
  }
  .brand-mark {
    display: flex; align-items: center; gap: 12px;
    margin-bottom: 22px;
  }
  .brand-mark__dot {
    width: 34px; height: 34px; border-radius: 50%;
    background: var(--ink-soft);
  }
  .brand-mark__name {
    font-weight: 700; font-size: 34px; letter-spacing: .5px;
    color: var(--ink-soft);
  }
  .slogan {
    font-weight: 700; font-size: 19px; letter-spacing: .6px;
    text-transform: uppercase; color: var(--ink-soft);
  }
  .slogan-rule {
    width: 300px; height: 1px; background: var(--ink-muted);
    margin: 8px 0 7px;
  }
  .services {
    font-size: 14px; color: var(--ink-muted);
  }

  /* Contact side */
  .card--contact {
    display: flex; align-items: center; justify-content: center;
    font-family: "PT Sans", sans-serif;
  }
  .person {
    text-align: right; padding-right: 16px;
    font-size: 13.5px; line-height: 1.3; color: var(--ink-soft);
  }
  .person__name {
    font-weight: 700; font-size: 17px; color: var(--ink); letter-spacing: .4px;
    text-transform: uppercase;
  }
  .person__role { font-size: 14px; margin-bottom: 2px; }
  .divider { width: 2px; height: 82px; background: var(--ink); }
  .contacts {
    list-style: none; padding-left: 14px;
    font-size: 14px; line-height: 1.45; color: var(--ink);
  }
  .contacts li { display: flex; align-items: center; gap: 7px; white-space: nowrap; }
  .contacts svg { width: 12px; height: 12px; fill: var(--ink); flex: none; }
</style>
</head>
<body>
<main class="canvas">
  <section class="card card--brand" aria-label="Card front">
    <div class="brand-mark">
      <span class="brand-mark__dot"></span>
      <span class="brand-mark__name">Brisk's Polish Works</span>
    </div>
    <p class="slogan">We make every mile shine</p>
    <div class="slogan-rule"></div>
    <p class="services">we detail anything with wheels, from daily drivers to campers</p>
  </section>

  <section class="card card--contact" aria-label="Card back">
    <div class="person">
      <p class="person__name">Marcus Hale</p>
      <p class="person__role">President</p>
      <p>3847 E Larkin Ave</p>
      <p>Carrow Falls ID 83714</p>
    </div>
    <div class="divider"></div>
    <ul class="contacts">
      <li>
        <svg viewBox="0 0 12 12" aria-hidden="true"><path d="M1 4c0-2 2-3 5-3s5 1 5 3H8.5V3h-5v1zM2.5 5h7l1 6h-9z"/></svg>
        208.417.6352
      </li>
      <li>
        <svg viewBox="0 0 12 12" aria-hidden="true"><path d="M3 0h6v12H3zM4 1.5v7.5h4V1.5z"/></svg>
        208 553 7190
      </li>
      <li>
        <svg viewBox="0 0 12 12" aria-hidden="true"><path d="M0 2h12v8H0zM1 3l5 4 5-4z"/></svg>
        BrisksPolish@mailvexo.com
      </li>
      <li>
        <svg viewBox="0 0 12 12" aria-hidden="true"><circle cx="6" cy="6" r="6"/></svg>
        www.briskspolishworks.com
      </li>
    </ul>
  </section>
</main>
</body>
</html>
```